Brookvane Consulting Business Card Design

Business Card Design for Brookvane Consulting. Brookvane Consulting is a boutique consultancy based in Atlanta, GA., that specializes in marketing strategy, organization planning, and leadership development. We provide solutions for small businesses and startups as well as Vantage 300 companies.

http://brookvaneconsulting.com/

Target Market(s)

We provide solutions for small businesses and startups as well as Vantage 300 companies.

Industry/Entity Type

Consulting

Contact Information for Business Card

Two sided business card with priority on contact information, logo, tag line (Clear Thinking to Plan Well, Lead Well, Grow Well)

Colors

Designer to choose colors to be used in the design.

Requirements
Must have
• contact information, logo, tag line (Clear Thinking to Plan Well, Lead Well, Grow Well)
• Simple no over communication.
Nice to have
• I would like to see different placements of logo and creative use of both sides of the card
Should not have
• Do not put too much information on the card.

```html
<!DOCTYPE html>
<html lang="en">
<head>
<meta charset="utf-8">
<title>Brookvane Consulting Business Card</title>
<link rel="stylesheet" href="https://fonts.googleapis.com/css2?family=Roboto:wght@400;500&family=Roboto+Condensed:wght@500&display=swap">
<style>
  :root {
    --page-bg: #d6d6d6;
    --card-dark: #1c1c1d;
    --card-back: #242424;
    --card-light: #ffffff;
    --text-light: #f2f2f2;
    --text-muted: #d9d9d9;
    --text-dark: #1e1e1e;
  }
  * { margin: 0; padding: 0; box-sizing: border-box; }
  html, body { width: 1200px; height: 960px; overflow: hidden; }
  body {
    background: var(--page-bg);
    position: relative;
    font-family: "Roboto", Arial, sans-serif;
  }
  .card {
    position: absolute;
    width: 600px;
    height: 342px;
    box-shadow: 0 3px 8px rgba(0,0,0,0.35);
    overflow: hidden;
  }
  .card-front { left: 314px; top: 113px; background: var(--card-light); }
  .card-back { left: 312px; top: 472px; }

  .front-top {
    position: absolute; left: 0; top: 0;
    width: 600px; height: 256px;
    background: var(--card-dark);
  }
  .front-notch { position: absolute; left: 88px; top: 255px; }

  .brand-name {
    position: absolute;
    color: var(--text-light);
    font-family: "Roboto", Arial, sans-serif;
    font-weight: 500;
    white-space: nowrap;
    letter-spacing: 0.5px;
  }
  .card-front .brand-name { left: 35px; top: 52px; font-size: 34px; }

  .contact-list {
    position: absolute; left: 35px; top: 147px;
    list-style: none;
    color: var(--text-light);
    font-size: 14px;
    line-height: 19.5px;
  }
  .contact-list li { display: flex; align-items: center; }
  .contact-list svg { width: 12px; height: 12px; margin-right: 10px; fill: var(--text-muted); }

  .tagline {
    position: absolute; left: 34px; top: 209px;
    color: var(--text-light);
    font-size: 14.5px;
    white-space: nowrap;
  }

  .person-name {
    position: absolute; left: 35px; top: 280px;
    font-family: "Roboto Condensed", "Arial Narrow", sans-serif;
    font-weight: 500;
    font-size: 21px;
    color: var(--text-dark);
  }
  .person-title {
    position: absolute; left: 35px; top: 306px;
    font-size: 15px; font-weight: 500;
    color: var(--text-dark);
  }

  .back-texture {
    position: absolute; inset: 0;
    background: linear-gradient(135deg, #262626, var(--card-back) 50%, #1f1f1f);
  }
  .card-back .brand-name {
    left: 0; width: 600px; top: 148px;
    text-align: center;
    font-size: 38px;
  }
</style>
</head>
<body>
  <section class="card card-front">
    <div class="front-top"></div>
    <svg class="front-notch" width="26" height="13" viewBox="0 0 26 13" aria-hidden="true">
      <polygon points="0,0 26,0 13,13" fill="#1c1c1d"/>
    </svg>
    <p class="brand-name">Brookvane Consulting</p>
    <ul class="contact-list">
      <li>
        <svg viewBox="0 0 12 12" aria-hidden="true"><path d="M2.3 0.5 L4.3 2.8 L3.2 4.1 C3.9 5.7 5.3 7.2 7.9 8.8 L9.2 7.7 L11.5 9.7 L10.1 11.5 C5.5 10.9 1.1 6.5 0.5 1.9 Z"/></svg>
        424-555-0142
      </li>
      <li>
        <svg viewBox="0 0 12 12" aria-hidden="true"><path d="M0.5 2.5 H11.5 V9.5 H0.5 Z M1.3 3.2 L6 6.6 L10.7 3.2 Z" fill-rule="evenodd"/></svg>
        darius@brookvaneconsulting.com
      </li>
      <li>
        <svg viewBox="0 0 12 12" aria-hidden="true"><circle cx="6" cy="6" r="5.5"/></svg>
        brookvaneconsulting.com
      </li>
    </ul>
    <p class="tagline">Clear Thinking to Plan Well, Lead Well, Grow Well</p>
    <p class="person-name">DARIUS WHITFIELD</p>
    <p class="person-title">Founder/Managing Director</p>
  </section>

  <section class="card card-back">
    <div class="back-texture" role="img" aria-label="Subtle dark grid pattern covering the back of the card"></div>
    <p class="brand-name">Brookvane Consulting</p>
  </section>
</body>
</html>
```